Business Card Re-Design/Update

We'd like to update out business cards. I've included our current "Style guide" which has the colour scheme of the organisation in it. I've also included the branding files with logos etc in them.

I've also included a copy of one of our existing cards so that you can see how ugly/dated they look. I'd like a fresh modern corporate look.

Target Market(s)

These are for our clients, potential clients, industry contacts - like all business cards

Contact Information for Business Card

Name
Position
Company Address - Level 1, 47 Fernby Street, Carlow Qld 4072
Direct Phone
mobile
Email
Website -www.korvalit.com.au
Logo

Colors

Designer to choose colors to be used in the design.

Requirements
Must have
• Main Logo
• Cards will need to be editable to be able to personalize them for each new employee.
Nice to have
• The MapOut, ShipWell, KeepSteady would be okay to have if they can be sensibly and professionally added to the look without detracting from the main imagery.
• Maybe they could go on the back of the card? will leave this to your creative discretion as to whether/where they fit.
Should not have
• Should not have decorative or script fonts

```html
<!DOCTYPE html>
<html lang="en">
<head>
<meta charset="utf-8">
<title>korvalIT business card</title>
<link rel="stylesheet" href="https://fonts.googleapis.com/css2?family=Nunito+Sans:wght@700&family=Roboto:wght@400&family=Roboto+Condensed:wght@400;700&display=swap">
<style>
  :root {
    --backdrop: #e4e4e4;
    --card-white: #f6f6f6;
    --brand-red: #d0161e;
    --brand-red-dark: #9e0c12;
    --ink: #222222;
    --ink-soft: #555555;
    --white: #ffffff;
  }
  * { margin: 0; padding: 0; box-sizing: border-box; }
  html, body { width: 1200px; height: 960px; overflow: hidden; }
  body { background: var(--backdrop); position: relative; font-family: "Roboto", Arial, sans-serif; }

  .card { position: absolute; width: 600px; height: 343px; overflow: hidden; }

  /* Front */
  .card-front { left: 314px; top: 113px; background: var(--card-white); }
  .side-band {
    position: absolute; left: 0; top: 0; width: 68px; height: 100%;
    background: linear-gradient(180deg, var(--brand-red), var(--brand-red-dark));
  }
  .brand {
    position: absolute; display: flex; align-items: center;
    font-family: "Nunito Sans", Arial, sans-serif; font-weight: 700; letter-spacing: -0.5px;
  }
  .brand-mark { flex: none; }
  .card-front .brand { left: 40px; top: 52px; font-size: 40px; color: var(--ink); gap: 24px; }
  .card-front .brand-mark { width: 40px; height: 40px; background: var(--brand-red); }

  .person { position: absolute; left: 118px; top: 108px; }
  .person-name {
    font-family: "Roboto Condensed", Arial, sans-serif; font-weight: 700;
    font-size: 21px; color: var(--brand-red); letter-spacing: 0.3px; line-height: 24px;
  }
  .person-role {
    font-family: "Roboto Condensed", Arial, sans-serif; font-weight: 400;
    font-size: 14.5px; color: var(--ink); line-height: 18px;
  }

  .contact-list { position: absolute; right: 40px; top: 175px; list-style: none; text-align: right; }
  .contact-list li {
    display: flex; justify-content: flex-end; align-items: center; gap: 7px;
    font-size: 14px; color: var(--ink-soft); line-height: 19.2px;
  }
  .contact-list svg { width: 13px; height: 13px; fill: var(--brand-red); flex: none; }
  .address { position: absolute; right: 38px; top: 291px; font-size: 14px; color: var(--ink-soft); }

  /* Back */
  .card-back {
    left: 311px; top: 472px;
    background: linear-gradient(180deg, var(--brand-red) 0%, var(--brand-red-dark) 100%);
  }
  .card-back .brand { left: 100px; top: 122px; font-size: 50px; color: var(--white); gap: 26px; }
  .card-back .brand-mark { width: 60px; height: 60px; background: var(--white); }

  .service-list {
    position: absolute; left: 52px; top: 278px; list-style: none;
    display: flex; gap: 36px;
  }
  .service-list li {
    display: flex; align-items: center; gap: 8px;
    font-family: "Nunito Sans", Arial, sans-serif; font-weight: 700;
    font-size: 25px; color: var(--white); letter-spacing: -0.3px;
  }
  .service-list li::before {
    content: ""; width: 22px; height: 22px; border: 3px solid var(--white);
  }
</style>
</head>
<body>

<section class="card card-front" aria-label="Card front">
  <div class="side-band"></div>
  <div class="brand"><span class="brand-mark"></span><span class="brand-name">korvalIT</span></div>
  <div class="person">
    <p class="person-name">MAREN HOLLOWAY</p>
    <p class="person-role">Business Development Manager</p>
  </div>
  <ul class="contact-list">
    <li>+61 (0)7 3840 2611
      <svg viewBox="0 0 24 24" aria-hidden="true"><path d="M6.6 10.8a15 15 0 0 0 6.6 6.6l2.2-2.2c.3-.3.7-.4 1-.2 1.1.4 2.3.6 3.6.6.6 0 1 .4 1 1V20c0 .6-.4 1-1 1A17 17 0 0 1 3 4c0-.6.4-1 1-1h3.5c.6 0 1 .4 1 1 0 1.3.2 2.5.6 3.6.1.3 0 .7-.2 1z"/></svg></li>
    <li>+61 (0)7 3840 2624
      <svg viewBox="0 0 24 24" aria-hidden="true"><path d="M6.6 10.8a15 15 0 0 0 6.6 6.6l2.2-2.2c.3-.3.7-.4 1-.2 1.1.4 2.3.6 3.6.6.6 0 1 .4 1 1V20c0 .6-.4 1-1 1A17 17 0 0 1 3 4c0-.6.4-1 1-1h3.5c.6 0 1 .4 1 1 0 1.3.2 2.5.6 3.6.1.3 0 .7-.2 1z"/></svg></li>
    <li>+61 (0)412 507 389
      <svg viewBox="0 0 24 24" aria-hidden="true"><path d="M7 1h10a2 2 0 0 1 2 2v18a2 2 0 0 1-2 2H7a2 2 0 0 1-2-2V3a2 2 0 0 1 2-2zm0 3v14h10V4z"/></svg></li>
    <li>+61 (0)7 3840 2650
      <svg viewBox="0 0 24 24" aria-hidden="true"><path d="M6 2h9l3 3v4H6zM3 10h18a1 1 0 0 1 1 1v8a1 1 0 0 1-1 1H3a1 1 0 0 1-1-1v-8a1 1 0 0 1 1-1zm3 3v2h12v-2z"/></svg></li>
    <li>mholloway@korvalit.com.au
      <svg viewBox="0 0 24 24" aria-hidden="true"><path d="M2 5h20v14H2zm2 2v.5l8 5 8-5V7z"/></svg></li>
    <li>www.korvalit.com.au
      <svg viewBox="0 0 24 24" aria-hidden="true"><path d="M12 2a10 10 0 1 0 0 20 10 10 0 0 0 0-20zm-1 17.9A8 8 0 0 1 4.2 10L9 14.8v1a2 2 0 0 0 2 2zm6.9-2.5A2 2 0 0 0 16 16h-1v-3a1 1 0 0 0-1-1H8v-2h2a1 1 0 0 0 1-1V7h2a2 2 0 0 0 2-2v-.4a8 8 0 0 1 2.9 12.8z"/></svg></li>
  </ul>
  <p class="address">Level 1, 47 Fernby Street, Carlow Qld 4072</p>
</section>

<section class="card card-back" aria-label="Card back">
  <div class="brand"><span class="brand-mark"></span><span class="brand-name">korvalIT</span></div>
  <ul class="service-list">
    <li>MapOut</li>
    <li>ShipWell</li>
    <li>KeepSteady</li>
  </ul>
</section>

</body>
</html>
```